Business Card Design needed - Something Awesome!

Need a business card designed. Company is "Marlowe Advisory" we do consulting and also have sales automation technology.
I'm going to use thick stock or metal, something really nice... I was thinking about a QR Code on the back that would just upload my contact info to the persons contact, etc -

This is a Strategy Company with a tech feel. I'm open to ideas but really want this to be nice!

I need a template that should include:

Name | Position or Title
D: 415.902.3376
www.marloweadvisory.example

I'm going to attach my contact so you can use that one, I need to get this printed.

Target Market(s)

Small to mid size customers, Entrepreneurs etc.

Industry/Entity Type

Consulting, Tech, Private Equity.

Contact Information for Business Card

Name, Phone, Maybe email, URL

Font styles to use
Sans Serif

Colors

Designer to choose only greyscale colors for use in the design.

Requirements
Must have
• Fresh, Clean, stand out from the crowd - will be on thick stock or metal.
Nice to have
• Clean, simple yet impactful.
Should not have
• Not cartoonish

```html
<!DOCTYPE html>
<html lang="en">
<head>
<meta charset="utf-8">
<title>Marlowe Advisory — Business Card</title>
<link rel="stylesheet" href="https://fonts.googleapis.com/css2?family=Lato:wght@400;700&display=swap">
<style>
  :root {
    --backdrop: #6a3e29;
    --card-light: #161b20;
    --card-dark: #020203;
    --silver: #bdbdc0;
    --silver-soft: #a9a9ad;
    --shadow: rgba(0, 0, 0, 0.45);
  }
  * { box-sizing: border-box; margin: 0; padding: 0; }
  html, body {
    width: 1200px;
    height: 1200px;
    overflow: hidden;
  }
  body {
    position: relative;
    background: var(--backdrop);
    font-family: "Lato", sans-serif;
  }
  .card {
    position: absolute;
    left: 251px;
    width: 699px;
    height: 399px;
    border-radius: 14px;
    background: linear-gradient(115deg, var(--card-light) 0%, #0b0d10 45%, var(--card-dark) 100%);
    box-shadow: 0 2px 6px var(--shadow);
    color: var(--silver);
    text-align: center;
  }
  .card--front { top: 159px; }
  .card--back { top: 644px; }

  .holder-name {
    position: absolute;
    top: 76px;
    left: 0; right: 0;
    font-size: 28px;
    font-weight: 700;
    letter-spacing: 0.5px;
    text-transform: uppercase;
  }
  .holder-title {
    position: absolute;
    top: 116px;
    left: 0; right: 0;
    font-size: 17px;
    font-weight: 400;
    color: var(--silver-soft);
  }
  .brand-mark {
    position: absolute;
    top: 183px;
    left: 0; right: 0;
    display: flex;
    justify-content: center;
    align-items: center;
    gap: 10px;
    font-size: 15px;
    font-weight: 700;
    letter-spacing: 3px;
    text-transform: uppercase;
  }
  .brand-mark__square {
    width: 12px;
    height: 12px;
    background: var(--silver);
  }
  .contact-phone {
    position: absolute;
    top: 263px;
    left: 0; right: 0;
    font-size: 23px;
    font-weight: 700;
  }
  .contact-email,
  .contact-web {
    position: absolute;
    left: 0; right: 0;
    font-size: 16px;
    font-weight: 400;
    color: var(--silver-soft);
    letter-spacing: 0.3px;
  }
  .contact-email { top: 297px; }
  .contact-web { top: 322px; }

  .wordmark {
    position: absolute;
    top: 142px;
    left: 0; right: 0;
    font-size: 96px;
    line-height: 1;
    font-weight: 400;
    letter-spacing: 2px;
    text-transform: uppercase;
  }
</style>
</head>
<body>
  <section class="card card--front">
    <h1 class="holder-name">Dorian K.Hale</h1>
    <p class="holder-title">Founder/CEO</p>
    <div class="brand-mark">
      <span class="brand-mark__square"></span>
      <span class="brand-mark__name">Marlowe Advisory</span>
    </div>
    <p class="contact-phone">415.902.3376</p>
    <p class="contact-email">hello@marloweadvisory.example</p>
    <p class="contact-web">marloweadvisory.example</p>
  </section>

  <section class="card card--back">
    <p class="wordmark">Marlowe</p>
  </section>
</body>
</html>
```